KTMR Website and Inner page template

Home page website design with inner page design for template. Details below as well as in txt document included
Project Description: New website for a current client ( KTMR ) .. current website is located at https://www.ktmr-board.org/Home.aspx
I need a home page design with an inner page design that will be used as a template ( 2 pages )
Logo is attached
Important notes:
Every page has to include the mission and vision. See below
"Our mission: to protect the public by promoting excellence in chiropractic regulation through service to our member boards
Our vision: The KTMR is the premier international resource for information and consolidated services for ensuring the safe, ethical practice of chiropractic"
Social media icons on the head of every page
facebook
twitter
linkedin
instagram
youtube
Every page needs to include the phone number on the header and footer
Main navigation links ( they are going to be different from current website ). Since most of these links are going to have sub-menus, please show the rollover affect. I have included the sub-menu options for "Get Started". The sub-menu should not be in a "list style" because the sub-menu links are categorized in some cases. A good example on their current website is to roll over the "Services" link in the main navigation
"Get Started" Sub-menu options ( categories and links )
- Chiropractic Regulators
- Annual Meeting
- District Meetings
- Licensing Board Information
- Library
- Administrators ( DRVOM )
- Legal Advisors ( DRVOM )
- Other Chiropractic Organizations
- Chiropractic Patients
- How to check a license
- Look up a license
- Request a Disciplinary Report
- Consumer Information
- Registered Chiropractors & Chiropractic Assistants
- Continuing Education Courses
- Chiropractic Assistant
- Certification
- View your continuing Ed Credits
Full list if primary navigation links:
Home
Contact
Company Info
Chiropractic Boards
Resources
Services
Get Started
Home Page Specifics:
"Hero Banner" or large "Slider" image with text at top of page below main navigation
4 primary points of interest to highlight
- TEP-ROW ( therapist event portal registry of warnings )
- ROVE ( Registry of Vetted Ongoing Learning )
- MSDV ( Member Spinal Desk Volunteers )
- Lanternway ( Open Ledger of Practitioner Standing )
Large "Member Access" area with the following links inside it
- Register for meetings
- Pay an Invoice
- TEP-ROW
- ROVE
- MSDV
- Report to TEP-ROW
- DRVOM Login
Large "Get Started" section with 3 categories that have links
- Chiropractic Regulators
- Annual Meeting
- District Meetings
- Library
- Chiropractic Patients
- How to Check a license
- Look up a license
- Consumer Information
- Coninuing Education Courses
- Chiropractic Assistant
- Certification
- View Your Continuing Ed Credits
Inner page specifics:
The inner page should look similar to the home page at the header and footer areas then have a large area for content. No large images or anything like that needed..
IMPORTANT... ONLY USE GRAPHICS/IMAGES from pixmeadow. ( https://www.pixmeadowimages.com/ ) This is important because we have an account with them so you can use the watermarked images then when I build the website I can easily purchase the licensing rights for those images. You dont' need an account to do searches, locate images and use the water marked image in the design.
Target Market(s)
Chiropractic Licensing
Number of Pages Required
2 page
Requirements
Must have
- Please see attached document
Nice to have
Should not have

```html
<!DOCTYPE html>
<html lang="en">
<head>
<meta charset="utf-8">
<title>KTMR — Home</title>
<link rel="stylesheet" href="https://fonts.googleapis.com/css2?family=Open+Sans:wght@400;600;700&family=Hind:wght@400;500;600;700&display=swap">
<style>
:root{
  --blue:#1f4a9c;
  --blue-band:#4372bb;
  --ink:#222;
  --text:#333;
  --muted:#555;
  --nav-bg:#e4e4e6;
  --light:#ebebeb;
  --white:#fff;
}
*{box-sizing:border-box;margin:0;padding:0}
html,body{width:1200px;height:2822px;overflow:hidden}
body{position:relative;font-family:"Hind","Open Sans",sans-serif;color:var(--text);background:var(--white)}
a{color:inherit;text-decoration:none}
.abs{position:absolute}

/* header */
.brand{left:112px;top:22px;display:flex;align-items:center;gap:10px}
.brand-mark{width:50px;height:50px;background:var(--blue)}
.brand-name{font-family:"Hind",sans-serif;font-size:22px;line-height:20px;color:var(--blue);font-weight:500}
.header-phone{left:680px;top:30px;display:flex;align-items:center;gap:8px;font-family:"Open Sans",sans-serif;font-size:26px;font-weight:700;color:#222}
.social{display:flex;gap:5px}
.social span{display:block;width:32px;height:32px;border-radius:50%;background:var(--blue)}
.header-social{left:910px;top:30px}

/* nav */
.nav{left:0;top:93px;width:1200px;height:44px;background:var(--nav-bg)}
.nav a{position:absolute;top:14px;font-size:13.5px;letter-spacing:.4px;color:#333;font-family:"Open Sans",sans-serif}
.nav .active{color:var(--blue);border-bottom:2px solid var(--blue);padding-bottom:6px}
.nav .cta{top:8px;left:982px;width:106px;height:28px;background:var(--blue);color:#fff;text-align:center;line-height:28px}

/* hero */
.hero{left:0;top:137px;width:1200px;height:594px;background:linear-gradient(100deg,#8f9499 0%,#b9bcc0 45%,#d8d6d2 70%,#9ea3a8 100%)}
.hero-card{left:112px;top:258px;width:413px;height:291px;background:rgba(225,225,228,.92);padding:26px 30px}
.hero-card h1{font-size:35px;line-height:40px;font-weight:600;color:#2a2a2a}
.hero-card p{margin-top:10px;font-size:16.5px;line-height:20px;color:#444}
.btn-learn{display:inline-block;margin-top:22px;background:var(--blue);color:#fff;font-family:"Open Sans",sans-serif;font-weight:700;font-size:12.5px;padding:11px 18px}
.dots{left:570px;top:680px;display:flex;gap:9px}
.dots span{width:8px;height:8px;border-radius:50%;background:#fff}
.dots span:first-child{background:var(--blue)}

/* welcome */
.welcome{left:0;top:786px;width:1200px;text-align:center}
.welcome h2{font-size:33px;font-weight:400;color:#333}
.welcome h3{font-size:28px;font-weight:400;color:var(--blue);margin-top:24px}
.welcome p{font-size:15px;line-height:25px;color:#333;margin-top:6px}

/* highlights */
.highlights{left:0;top:1124px;width:1200px;height:349px;background:linear-gradient(160deg,#3f68ad 0%,#4a77be 60%,#3c6ab6 100%)}
.feature{position:absolute;top:80px;width:240px;text-align:center;color:#fff}
.feature .name{height:60px;display:flex;align-items:center;justify-content:center;font-size:22px;font-weight:600;letter-spacing:1px}
.feature .title{margin-top:16px;font-size:14px;font-weight:600;line-height:23px;text-decoration:underline}
.feature .desc{margin-top:6px;font-size:11.5px;line-height:23px;font-family:"Open Sans",sans-serif}

/* member access */
.member{left:0;top:1473px;width:1200px;height:310px;background:var(--light);text-align:center}
.member h2{margin-top:64px;font-size:33px;font-weight:700;color:var(--blue)}
.member-links{position:absolute;top:153px;left:118px;display:flex;gap:10px}
.member-links a{height:59px;line-height:59px;padding:0 16px;background:#fff;color:var(--blue);font-size:17px;box-shadow:0 1px 3px rgba(0,0,0,.12)}

/* get started */
.started{left:0;top:1783px;width:1200px;height:662px;background:#fbfbfc}
.started h2{position:absolute;top:52px;width:1200px;text-align:center;font-size:33px;font-weight:700;color:var(--blue)}
.group{position:absolute;top:146px;width:300px;text-align:center}
.group .icon{width:138px;height:138px;border-radius:50%;border:3px solid var(--blue);margin:0 auto;display:flex;align-items:center;justify-content:center;background:#fff}
.group .icon span{width:124px;height:124px;border-radius:50%;background:var(--blue);display:flex;align-items:center;justify-content:center}
.group h3{margin-top:20px;font-size:22px;font-weight:600;color:#222}
.group ul{list-style:none;margin-top:12px}
.group li{font-size:14.5px;line-height:30px;color:#333}
.group li::before{content:"";display:inline-block;width:11px;height:11px;border-radius:50%;background:var(--blue);margin-right:5px;vertical-align:-1px}

/* footer */
.footer{left:0;top:2445px;width:1200px;height:377px;background:var(--blue);color:#fff}
.fcol{position:absolute;top:60px}
.fcol h4{font-size:19px;font-weight:600}
.fcol ul{list-style:none;margin-top:18px}
.fcol li{font-size:14px;line-height:31px}
.contact-row{display:flex;gap:12px;font-size:14px;line-height:31px}
.contact-row svg{margin-top:8px;flex:none}
.footer .social span{background:none;border:2px solid #fff}
.footer-bottom{position:absolute;top:312px;left:0;width:1200px;border-top:1px solid rgba(255,255,255,.25);height:65px}
.copy{position:absolute;left:111px;top:20px;font-size:13.5px}
.legal{position:absolute;left:905px;top:22px;font-size:10.5px;color:#7d97c8}
</style>
</head>
<body>

<header>
  <div class="abs brand">
    <span class="brand-mark"></span>
    <span class="brand-name">Kinetic Therapy<br>Membership<br>Registry</span>
  </div>
  <div class="abs header-phone">
    <svg width="24" height="24" viewBox="0 0 24 24"><path fill="#1f4a9c" d="M6.6 10.8a15 15 0 0 0 6.6 6.6l2.2-2.2c.3-.3.7-.4 1-.2 1.1.4 2.3.6 3.6.6.6 0 1 .4 1 1V20c0 .6-.4 1-1 1A17 17 0 0 1 3 4c0-.6.4-1 1-1h3.5c.6 0 1 .4 1 1 0 1.3.2 2.5.6 3.6.1.3 0 .7-.2 1z"/></svg>
    555.214.3800
  </div>
  <div class="abs social header-social" aria-label="Social media links"><span></span><span></span><span></span><span></span><span></span></div>
</header>

<nav class="abs nav">
  <a class="active" style="left:118px">HOME</a>
  <a style="left:221px">COMPANY INFO</a>
  <a style="left:385px">CHIROPRACTIC BOARDS</a>
  <a style="left:600px">RESOURCES</a>
  <a style="left:738px">SERVICES</a>
  <a style="left:859px">CONTACT</a>
  <a class="cta">GET STARTED</a>
</nav>

<section class="abs hero" role="img" aria-label="Smiling practitioner in a white coat reaching out for a handshake"></section>
<div class="abs hero-card">
  <h1>Kinetic Therapy<br>Membership<br>Registry</h1>
  <p>The KTMR is the premier international resource for information and consolidated services</p>
  <a class="btn-learn">LEARN MORE &rsaquo;</a>
</div>
<div class="abs dots"><span></span><span></span><span></span><span></span></div>

<section class="abs welcome">
  <h2>Welcome to Kinetic Therapy Membership Registry</h2>
  <h3>Our mission</h3>
  <p>To protect the public by promoting excellence in chiropractic regulation through service to our member boards</p>
  <h3>Our vision</h3>
  <p>The KTMR is the premier international resource for information and consolidated services for ensuring the safe,<br>ethical practice of chiropractic</p>
</section>

<section class="abs highlights" role="img" aria-label="Faded blue-tinted handshake photograph">
  <div class="feature" style="left:102px">
    <div class="name">TEP-ROW</div>
    <div class="title">TEP-ROW - Therapist Event Portal<br>Registry of Warnings</div>
    <div class="desc">A repository of all chiropractic licensing<br>boards' disciplinary actions</div>
  </div>
  <div class="feature" style="left:358px">
    <div class="name">ROVE</div>
    <div class="title">ROVE - Registry of Vetted<br>Ongoing Learning</div>
    <div class="desc">Search for courses or download<br>a transcript</div>
  </div>
  <div class="feature" style="left:616px">
    <div class="name">MSDV</div>
    <div class="title">MSDV - Member Spinal<br>Desk Volunteers</div>
    <div class="desc">Professional recognition &amp; national<br>certification</div>
  </div>
  <div class="feature" style="left:873px">
    <div class="name">Lanternway</div>
    <div class="title">Lanternway - Open Ledger of<br>Practitioner Standing</div>
    <div class="desc">Making healthcare portable</div>
  </div>
</section>

<section class="abs member">
  <h2>Member Access</h2>
  <div class="member-links">
    <a>Register for meetings</a><a>Pay an Invoice</a><a>TEP-ROW</a><a>ROVE</a><a>MSDV</a><a>Report to TEP-ROW</a><a>DRVOM Login</a>
  </div>
</section>

<section class="abs started">
  <h2>Get Started</h2>
  <div class="group" style="left:73px">
    <div class="icon"><span><svg width="56" height="60" viewBox="0 0 56 60"><rect x="4" y="4" width="48" height="52" fill="none" stroke="#fff" stroke-width="3"/><path d="M16 18v24M28 18v24M40 18v24" stroke="#fff" stroke-width="3"/></svg></span></div>
    <h3>Regulators</h3>
    <ul><li>Chiropractic Regulators</li><li>Annual Meeting</li><li>District Meetings</li><li>Licensing Board Information</li><li>Library</li><li>Administrators ( DRVOM )</li><li>Legal Advisors ( DRVOM )</li><li>Other Chiropractic Organizations</li></ul>
  </div>
  <div class="group" style="left:450px">
    <div class="icon"><span><svg width="60" height="60" viewBox="0 0 60 60"><circle cx="30" cy="14" r="7" fill="none" stroke="#fff" stroke-width="3"/><circle cx="16" cy="30" r="6" fill="none" stroke="#fff" stroke-width="3"/><circle cx="44" cy="30" r="6" fill="none" stroke="#fff" stroke-width="3"/><path d="M6 54v-8a10 10 0 0 1 20 0v8M34 54v-8a10 10 0 0 1 20 0v8" fill="none" stroke="#fff" stroke-width="3"/></svg></span></div>
    <h3>Public</h3>
    <ul><li>Chiropractic Patients</li><li>How to Check a license</li><li>Look up a license</li><li>Request a Disciplinary Report</li><li>Consumer Information</li></ul>
  </div>
  <div class="group" style="left:805px">
    <div class="icon"><span><svg width="56" height="60" viewBox="0 0 56 60"><rect x="6" y="4" width="36" height="50" fill="none" stroke="#fff" stroke-width="3"/><path d="M14 36h20M14 44h14" stroke="#fff" stroke-width="3"/><circle cx="24" cy="20" r="7" fill="none" stroke="#fff" stroke-width="3"/><path d="M50 20L36 48" stroke="#fff" stroke-width="4"/></svg></span></div>
    <h3>Professionals</h3>
    <ul><li>Registered Chiropractors &amp; Chiropractic<br>Assistants</li><li>Coninuing Education Courses</li><li>Chiropractic Assistant</li><li>Certification</li><li>View Your Continuing Ed Credits</li></ul>
  </div>
</section>

<footer class="abs footer">
  <div class="fcol" style="left:111px">
    <h4>Quick Links</h4>
    <ul><li>Home</li><li>Company Info</li><li>Chiropractic Boards</li><li>Resources</li><li>Services</li></ul>
  </div>
  <div class="fcol" style="left:351px">
    <h4>Company</h4>
    <ul><li>For Our Board</li><li>Query TEP-ROW</li><li>Login</li><li>Get Started</li><li>Contact</li></ul>
  </div>
  <div class="fcol" style="left:591px">
    <h4>Contact Us</h4>
    <div style="margin-top:18px">
      <div class="contact-row"><svg width="12" height="16" viewBox="0 0 12 16"><path fill="#fff" d="M6 0a6 6 0 0 0-6 6c0 4.5 6 10 6 10s6-5.5 6-10a6 6 0 0 0-6-6zm0 8.5A2.5 2.5 0 1 1 6 3.5a2.5 2.5 0 0 1 0 5z"/></svg><span>2180 Alder Crest Road, Suite 204<br>Brookhaven, CO &nbsp;80999</span></div>
      <div class="contact-row" style="margin-top:9px"><svg width="12" height="18" viewBox="0 0 12 18"><rect x="1" y="1" width="10" height="16" rx="2" fill="none" stroke="#fff" stroke-width="2"/></svg><span>555.214.3800</span></div>
      <div class="contact-row" style="margin-top:9px"><svg width="16" height="16" viewBox="0 0 24 24"><path fill="#fff" d="M6.6 10.8a15 15 0 0 0 6.6 6.6l2.2-2.2c.3-.3.7-.4 1-.2 1.1.4 2.3.6 3.6.6.6 0 1 .4 1 1V20c0 .6-.4 1-1 1A17 17 0 0 1 3 4c0-.6.4-1 1-1h3.5c.6 0 1 .4 1 1 0 1.3.2 2.5.6 3.6.1.3 0 .7-.2 1z"/></svg><span>555.214.3899</span></div>
    </div>
  </div>
  <div class="fcol" style="left:908px">
    <h4>Connect With Us</h4>
    <div class="social" style="margin-top:24px" aria-label="Social media links"><span></span><span></span><span></span><span></span><span></span></div>
  </div>
  <div class="footer-bottom">
    <div class="copy">Copyrights © 2021 &nbsp;Kinetic Therapy Membership Registry. All rights reserved.</div>
    <div class="legal">Terms and Conditions | Privacy Policy</div>
  </div>
</footer>

</body>
</html>
```